Hollow Mesa Farm Vault Reserve Wine Label (Front and Back)

I need to create an elite tier wine label.  I would like it to be in a light, natural color with silver or gold.  I would like it to look rich and expensive, mostly monochromatic, elegantly simple.  It will need to stand up next to wine labels that are black and charcoal colored and look like the more expensive wine of the 3.  I have attached a similar label that it will be grouped with and some instructions.
We are a winery in southeast Washington state with a reputation for fine wines and top notch terroir.  We want to present family, tradition and high value wine in the bottle.

```html
<!DOCTYPE html>
<html lang="en">
<head>
<meta charset="UTF-8">
<title>Hollow Mesa Farm – Vault Reserve Label</title>
<link rel="stylesheet" href="https://fonts.googleapis.com/css2?family=Cinzel:wght@400;600;700&family=Cormorant+Garamond:wght@500;600&family=Great+Vibes&display=swap">
<style>
  :root {
    --backdrop-top: #4a4e5b;
    --backdrop-bottom: #6b7080;
    --paper: #f2f1ee;
    --paper-edge: #e4e3df;
    --ink: #1d1d1f;
    --ink-soft: #3a3a3d;
    --gold: #c8902e;
    --gold-light: #e8c06a;
    --gold-deep: #a9741e;
    --silver: #cfd0d3;
  }
  * { margin: 0; padding: 0; box-sizing: border-box; }
  html, body {
    width: 918px;
    height: 1200px;
    overflow: hidden;
  }
  body {
    background: linear-gradient(180deg, var(--backdrop-top), var(--backdrop-bottom));
    display: flex;
    align-items: center;
    justify-content: center;
  }
  .label {
    width: 720px;
    height: 960px;
    background: linear-gradient(180deg, var(--paper), var(--paper-edge));
    display: flex;
    flex-direction: column;
    align-items: center;
    padding-top: 70px;
    position: relative;
    box-shadow: 0 18px 40px rgba(0,0,0,0.25);
  }
  .winery-name {
    font-family: "Cinzel", serif;
    font-weight: 400;
    font-size: 70px;
    line-height: 1.0;
    letter-spacing: 1px;
    color: var(--ink);
    text-align: center;
  }
  .appellation {
    font-family: "Cinzel", serif;
    font-weight: 400;
    font-size: 22px;
    letter-spacing: 6px;
    color: var(--ink-soft);
    margin-top: 34px;
  }
  .crest-row {
    display: flex;
    align-items: center;
    justify-content: center;
    gap: 14px;
    margin-top: 40px;
    width: 100%;
  }
  .crest-flank {
    width: 210px;
    height: 60px;
    background: linear-gradient(90deg, rgba(207,208,211,0), var(--silver) 50%, rgba(207,208,211,0.4));
    opacity: 0.7;
  }
  .crest-flank.right { transform: scaleX(-1); }
  .house-mark {
    display: flex;
    flex-direction: column;
    align-items: center;
    gap: 10px;
    width: 150px;
  }
  .house-mark-square {
    width: 22px;
    height: 22px;
    border: 2px solid var(--gold);
  }
  .house-mark-name {
    font-family: "Cinzel", serif;
    font-weight: 600;
    font-size: 17px;
    letter-spacing: 2px;
    color: var(--gold);
    text-align: center;
    line-height: 1.3;
  }
  .vineyard {
    font-family: "Cormorant Garamond", serif;
    font-weight: 600;
    font-size: 26px;
    letter-spacing: 1px;
    color: var(--ink-soft);
    margin-top: 56px;
  }
  .tier-name {
    font-family: "Cinzel", serif;
    font-weight: 700;
    font-size: 60px;
    letter-spacing: 1px;
    color: var(--ink);
    margin-top: 4px;
  }
  .varietal {
    font-family: "Great Vibes", cursive;
    font-size: 44px;
    color: var(--gold);
    margin-top: 2px;
  }
  .vintage {
    font-family: "Cormorant Garamond", serif;
    font-weight: 500;
    font-size: 26px;
    color: var(--ink-soft);
    margin-top: 20px;
  }
  .heritage-band {
    position: absolute;
    left: 0;
    right: 0;
    bottom: 62px;
    height: 42px;
    background: linear-gradient(180deg, var(--gold-light), var(--gold) 55%, var(--gold-deep));
    display: flex;
    align-items: center;
    justify-content: center;
  }
  .heritage-text {
    font-family: "Cormorant Garamond", serif;
    font-weight: 600;
    font-size: 20px;
    letter-spacing: 1px;
    color: var(--ink);
  }
</style>
</head>
<body>
  <main class="label">
    <h1 class="winery-name">HOLLOW MESA<br>FARM</h1>
    <p class="appellation">HORSE HEAVEN HILLS</p>

    <div class="crest-row">
      <div class="crest-flank left" role="img" aria-label="Silver geometric ornament"></div>
      <div class="house-mark">
        <span class="house-mark-square"></span>
        <span class="house-mark-name">HOLLOW MESA FARM</span>
      </div>
      <div class="crest-flank right" role="img" aria-label="Silver geometric ornament"></div>
    </div>

    <p class="vineyard">ESTATE VINEYARD</p>
    <h2 class="tier-name">VAULT RESERVE</h2>
    <p class="varietal">Cabernet Sauvignon</p>
    <p class="vintage">2022</p>

    <div class="heritage-band">
      <p class="heritage-text">FAMILY STEWARDS OF THE LAND FOR 5 GENERATIONS</p>
    </div>
  </main>
</body>
</html>
```